Healthcare and Professional IT Services Company need a redesigned business card

We are a IT Services company that targets small medical practices and professional business such as Attorneys, Accounts, Architects etc. We want to communicate a professional yet friendly image using recent logo redesign here on ArtHarbor. Like to see the colors blue and orange in the design. Must use the Tall Pine Computing as displayed in the new logo - then also want to incorporate the fish logo as well.

Target Market(s)

Small medical and professional services

Industry/Entity Type

It Company

Contact Information for Business Card

The usual stuff, place for name address phone website. Also maybe our tagline which is "hooked on technology"

Requirements
Must have
• My new logo and the fish somewhere on the card

```html
<!DOCTYPE html>
<html lang="en">
<head>
<meta charset="utf-8">
<title>Tall Pine Computing – Business Card</title>
<link rel="stylesheet" href="https://fonts.googleapis.com/css2?family=Arimo:wght@400;700&display=swap">
<style>
  :root {
    --stage: #e9e6e1;
    --card-black: #0b0b0c;
    --card-black-soft: #1a1a1c;
    --brand-blue: #2a8fd6;
    --brand-blue-deep: #1c73b8;
    --accent-orange: #c47a1c;
    --text-white: #f2f2f2;
  }
  * { box-sizing: border-box; margin: 0; padding: 0; }
  html, body { width: 1200px; height: 858px; overflow: hidden; }
  body {
    background: var(--stage);
    font-family: "Arimo", Arial, sans-serif;
    display: flex;
    align-items: center;
    justify-content: center;
    gap: 36px;
  }
  .card {
    position: relative;
    width: 540px;
    height: 310px;
    background: linear-gradient(135deg, var(--card-black-soft) 0%, var(--card-black) 55%);
    overflow: hidden;
    box-shadow: 0 10px 28px rgba(0,0,0,.25);
  }
  .card__band {
    position: absolute;
    left: 0; right: 0; bottom: 0;
    height: 26px;
    background: var(--brand-blue);
    border-top: 3px solid var(--accent-orange);
  }
  /* Front */
  .front__brand {
    position: absolute;
    left: 28px; top: 78px;
    width: 200px;
    display: flex;
    align-items: center;
    gap: 12px;
  }
  .brand__dot {
    flex: none;
    width: 22px; height: 22px;
    border-radius: 50%;
    background: var(--brand-blue);
  }
  .brand__name {
    color: var(--brand-blue);
    font-weight: 700;
    font-size: 30px;
    line-height: 1.05;
  }
  .front__divider {
    position: absolute;
    left: 240px; top: 32px;
    width: 2px; height: 220px;
    background: var(--accent-orange);
  }
  .front__details {
    position: absolute;
    left: 262px; top: 48px;
    right: 18px;
  }
  .person-name {
    color: var(--accent-orange);
    font-weight: 700;
    font-size: 28px;
    margin-bottom: 26px;
  }
  .contact-list { list-style: none; }
  .contact-list li {
    display: flex;
    align-items: center;
    gap: 10px;
    color: var(--text-white);
    font-size: 13px;
    line-height: 1;
    margin-bottom: 12px;
    white-space: nowrap;
  }
  .contact-icon {
    flex: none;
    width: 16px; height: 16px;
    background: var(--brand-blue);
    display: block;
  }
  /* Back */
  .back__brand {
    position: absolute;
    left: 0; right: 0; top: 0; bottom: 26px;
    display: flex;
    align-items: center;
    justify-content: center;
    gap: 16px;
  }
  .back__brand .brand__dot { width: 30px; height: 30px; }
  .back__brand .brand__name { font-size: 40px; }
</style>
</head>
<body>
  <section class="card card--front" aria-label="Business card front">
    <div class="front__brand">
      <span class="brand__dot"></span>
      <span class="brand__name">Tall Pine Computing</span>
    </div>
    <div class="front__divider"></div>
    <div class="front__details">
      <p class="person-name">Daniel Marwick</p>
      <ul class="contact-list">
        <li>
          <svg class="contact-icon" viewBox="0 0 16 16" aria-hidden="true"><rect width="16" height="16" fill="#2a8fd6"/><path d="M5 3.5h2l1 3-1.3 1a6 6 0 0 0 1.8 1.8l1-1.3 3 1v2c0 .6-.5 1-1 1A8.5 8.5 0 0 1 4 4.5c0-.6.4-1 1-1z" fill="#fff"/></svg>
          1300 555 012
        </li>
        <li>
          <svg class="contact-icon" viewBox="0 0 16 16" aria-hidden="true"><rect width="16" height="16" fill="#2a8fd6"/><rect x="3" y="4.5" width="10" height="7" fill="none" stroke="#fff" stroke-width="1.2"/><path d="M3 4.5l5 4 5-4" fill="none" stroke="#fff" stroke-width="1.2"/></svg>
          info@tallpinecomputing.com.au
        </li>
        <li>
          <svg class="contact-icon" viewBox="0 0 16 16" aria-hidden="true"><rect width="16" height="16" fill="#2a8fd6"/><circle cx="8" cy="8" r="4.8" fill="none" stroke="#fff" stroke-width="1.1"/><ellipse cx="8" cy="8" rx="2" ry="4.8" fill="none" stroke="#fff" stroke-width="1"/><path d="M3.2 8h9.6" stroke="#fff" stroke-width="1"/></svg>
          www.tallpinecomputing.com
        </li>
        <li>
          <svg class="contact-icon" viewBox="0 0 16 16" aria-hidden="true"><rect width="16" height="16" fill="#2a8fd6"/><path d="M8 13.5s-4-4.2-4-7a4 4 0 0 1 8 0c0 2.8-4 7-4 7z" fill="#fff"/><circle cx="8" cy="6.5" r="1.5" fill="#2a8fd6"/></svg>
          4410 Cedarfield Road Millbrook BC
        </li>
      </ul>
    </div>
    <div class="card__band"></div>
  </section>

  <section class="card card--back" aria-label="Business card back">
    <div class="back__brand">
      <span class="brand__dot"></span>
      <span class="brand__name">Tall Pine Computing</span>
    </div>
    <div class="card__band"></div>
  </section>
</body>
</html>
```